Specialized Personal Trainer Needs a Business Card Design

I need a business card design for my personal training business called Tall Oak Fitness. I have my Human Kinetics degree in Exercise Science from the Halvering Polytechnic Institute as well as an extra certification from NFBP (National Federation of Body Practice). I work as a Cardiac Rehab Exercise Specialist and personal trainer giving specialized exercise prescriptions to those that have different heart conditions as well as work with the general population in weight loss, strength and conditioning, getting/staying fit.
Updates

I decided that I wanted a logo (as I did not have one before I submitted my project for a business card) so I am submitting a project to get a logo done and then I will decide on a business card, hopefully being able to use one of the designs already submitted.  My apologies for doing this backwards.  I am new to this so I appreciate your patience.

Thank you.

Hi, I have just created a project for a logo design (I realized I needed a logo and I should've done that first..oops!), please feel free to participate.  Once I receive a logo I like I will finalize my business card project and hopefully incorporate it into one of your business card designs. 

Thank you!

Target Market(s)

Business professionals

Industry/Entity Type

Personal Trainer

Requirements
Must have
• My name with my info:
Delphine R. Ashcroft (BHK)
NFBP Certified Clinical Exercise Specialist & Personal Trainer
del.ashcroft@talloakfitness.example
Cell: 555-302-6148

Please make it double sided.
Nice to have
• An image that represents cardiac and general fitness training.

```html
<!DOCTYPE html>
<html lang="en">
<head>
<meta charset="utf-8">
<title>Tall Oak Fitness — Business Card</title>
<link href="https://fonts.googleapis.com/css2?family=Barlow:wght@400;500&family=Roboto+Condensed:wght@400;700&display=swap" rel="stylesheet">
<style>
  :root {
    --brand-red: #e31937;
    --ink-red: #e0203a;
    --paper: #ffffff;
    --page: #ffffff;
    --card-edge: #d6d8da;
    --card-shadow: rgba(0, 0, 0, 0.22);
  }
  * { margin: 0; padding: 0; box-sizing: border-box; }
  html, body {
    width: 1200px;
    height: 901px;
    overflow: hidden;
    background: var(--page);
  }
  .canvas {
    position: relative;
    width: 1200px;
    height: 901px;
  }
  .card {
    position: absolute;
    left: 258px;
    width: 692px;
    height: 395px;
    border-radius: 30px;
    box-shadow: 0 6px 8px var(--card-shadow);
    overflow: hidden;
  }
  .card--front {
    top: 40px;
    background: var(--brand-red);
    display: flex;
    align-items: center;
    justify-content: center;
  }
  .brand-name {
    font-family: "Roboto Condensed", sans-serif;
    font-weight: 700;
    color: var(--paper);
    text-transform: uppercase;
    text-align: center;
    font-size: 74px;
    line-height: 0.92;
    letter-spacing: -0.5px;
  }
  .card--back {
    top: 474px;
    background: var(--paper);
    border: 1px solid var(--card-edge);
    color: var(--ink-red);
  }
  .services {
    position: absolute;
    top: 52px;
    left: 0;
    right: 0;
    text-align: center;
    font-family: "Barlow", sans-serif;
    font-weight: 400;
    font-size: 17.5px;
    letter-spacing: 1px;
    text-transform: uppercase;
  }
  .services .divider { margin: 0 14px; }
  .identity {
    position: absolute;
    top: 141px;
    left: 0;
    right: 0;
    text-align: center;
    font-family: "Roboto Condensed", sans-serif;
  }
  .company {
    font-weight: 700;
    font-size: 39px;
    line-height: 1.1;
  }
  .person {
    margin-top: 12px;
    font-weight: 400;
    font-size: 29px;
    line-height: 1.1;
  }
  .person .credential { font-size: 20px; }
  .certification {
    margin-top: 2px;
    font-weight: 400;
    font-size: 20px;
    line-height: 1.2;
  }
  .contact {
    position: absolute;
    bottom: 22px;
    font-family: "Roboto Condensed", sans-serif;
    font-size: 23px;
    line-height: 28px;
  }
  .contact--web { left: 38px; }
  .contact--phone { right: 36px; }
</style>
</head>
<body>
<main class="canvas">
  <section class="card card--front" aria-label="Card front">
    <h1 class="brand-name">Tall Oak<br>Fitness</h1>
  </section>

  <section class="card card--back" aria-label="Card back">
    <p class="services">Training<span class="divider">|</span>Cardiac Rehabilitation<span class="divider">|</span>Wellness</p>
    <div class="identity">
      <h2 class="company">Tall Oak Fitness</h2>
      <p class="person">Delphine R. Ashcroft <span class="credential">(BHK)</span></p>
      <p class="certification">NFBP Certified Clinical Exercise Specialist &amp; Personal Trainer</p>
    </div>
    <p class="contact contact--web">www.talloakfitness.example<br>del.ashcroft@talloakfitness.example</p>
    <p class="contact contact--phone">555-302-6148</p>
  </section>
</main>
</body>
</html>
```